Etiketten für Ätherische Öle, Extrakte und Speiseöle gesucht
Zielgruppe
Wir verkaufen natürlich Produkte. Ätherische öle, Extrakte, Speise öle.
Wir verkaufen im Webshop, Korbix und auch im Betrieb.
https://www.natur-vemo.com
Wir verkaufen hauptsächlich innerhalb Italiens und Deutschland daher doppel sprachig.
Aufgabenstellung
Guten Tag
Bitte verwenden Sie! : * beispiel_10_ml_etikett_nachbau.jpg *
Da mir die kleinste Größe die wichtigste ist habe ich ein beispiel Hochgeladen. Das kleinste Etikett lässt sich öffnen und daher sind nur 7 cm ersichtlich und man muss das Etikett aufmachen.
Habe ein Beispiel Hochgeladen. Aber bitte einfach kreativ sein. *Anhang: beispiel Etikett*
Sobald ich eine Art vom kelinsten habe würde ich dies für die 2 anderen Größen übernehmen aber das man Sie irgendwie gut unterscheiden kann da dies dann komplett andere Produkte (Extrakte/Speise öl) sein werden.
Erstellung von drei unterschiedlichen Größen von Etiketten mit folgenden Eigenschaften:
Am wichtigsten ist mir das kleinste Etikett da dies auch am schwersten ist daher habe ich die anderen Größen nun gelöscht!
• 10 ml Länge: 155 mm Breite: 32 mm.
Brauche 3 unterschiedliche Grund Farben: z. B. Ätherische Öle (Grün) Extrakte (Rot) Speiseöle (gelb). Die Farben lasse ich sie entscheiden.
Die Etiketten müssen 2 Sprachen (Deutsch / Italienisch) sein deshalb muss dieses berücksichtigt werden.
Anbei finden Sie:
• Logo (Bild Logo)
• Beispiel Text ätherische Öle
• Bilder der aktuellen Flaschen
Unter https://www.natur-vemo.com/de finden Sie meine Seite
Anmerkung: Im Anhang: *Back*
Habe ich mein Logo mit Firmennamen ; Bio des Haubner Stefan
Da ich jedoch nicht alle Produkte im biologischen Anbau habe und mein Logo zu miss Verständnis führen könnte habe ich ein Bildliches Logo gemacht das ich fortan auf meinen Produkten haben möchte. Im besonderes dieses Grün das in beiden vorhanden ist versuche ich zu integrieren.
Habe selbst ein Etikett designet das aber sehr unprofessionell wirkt aber dieses Grüne das ich gerne als merkmal unterbringen würde.
Siehe Anhang: neemöl

```html
<!DOCTYPE html>
<html lang="de">
<head>
<meta charset="utf-8">
<title>Lavendel fein / Lavanda fine – 10 ml Etikett</title>
<link rel="stylesheet" href="https://fonts.googleapis.com/css2?family=Figtree:wght@400;600&family=Libre+Baskerville:wght@400&display=swap">
<style>
  :root {
    --page: #ffffff;
    --panel: #9db36b;
    --frame: #e0186c;
    --ink: #2b3590;
    --band-top: #ffffff;
    --band-bottom: #b5d12c;
    --field: #ffffff;
  }
  * { box-sizing: border-box; margin: 0; padding: 0; }
  html, body { width: 1200px; height: 330px; overflow: hidden; background: var(--page); }
  .canvas { position: relative; width: 1200px; height: 330px; }
  .label {
    position: absolute; left: 49px; top: 31px; width: 1101px; height: 252px;
    background: linear-gradient(to bottom, var(--band-top) 0%, var(--band-top) 28%, var(--band-bottom) 100%);
    font-family: "Figtree", sans-serif; color: var(--ink);
  }
  .panel { position: absolute; top: 0; height: 100%; background: var(--panel); }
  .panel--imprint { left: 0; width: 261px; }
  .panel--usage { right: 0; width: 294px; }
  .cut-frame {
    position: absolute; left: 7px; top: 14px; width: 1088px; height: 225px;
    border: 2px solid var(--frame); pointer-events: none;
  }

  .imprint { position: absolute; left: 19px; top: 44px; width: 236px; font-size: 9.5px; line-height: 11px; }
  .imprint__title { font-weight: 600; }
  .imprint__lot { margin-top: 8px; font-size: 8.5px; font-weight: 600; }
  .imprint__best { margin-top: 8px; font-size: 7.5px; font-weight: 600; }
  .best-before-field { position: absolute; left: 19px; top: 188px; width: 187px; height: 45px; background: var(--field); }

  .product { position: absolute; left: 261px; width: 546px; top: 0; height: 100%; text-align: center; }
  .product__art {
    position: absolute; left: 252px; top: 34px; width: 50px; height: 81px;
    background: radial-gradient(circle at 50% 35%, #c04fd8 0%, #6c5bd6 35%, #d8e6a8 70%, #c7d936 100%);
  }
  .product__name {
    position: absolute; left: 0; right: 0; top: 130px;
    font-family: "Libre Baskerville", serif; font-weight: 400; font-size: 38px; line-height: 44px;
    color: var(--ink);
    text-shadow: 0 0 3px #fff, 0 0 3px #fff, 0 0 4px #fff;
  }
  .product__variant {
    position: absolute; left: 0; right: 0; top: 178px;
    font-family: "Libre Baskerville", serif; font-size: 14px;
    text-shadow: 0 0 3px #fff, 0 0 3px #fff;
  }
  .product__volume { position: absolute; left: 0; right: 0; top: 207px; font-size: 14px; }

  .usage { position: absolute; left: 819px; width: 276px; top: 20px; font-size: 9.5px; line-height: 10.8px; }
  .usage b { font-weight: 600; }
  .usage__block + .usage__block { margin-top: 6px; }
</style>
</head>
<body>
<div class="canvas">
  <div class="label">
    <div class="panel panel--imprint"></div>
    <div class="panel panel--usage"></div>

    <div class="imprint">
      <p class="imprint__title">Firmenname / Ragione sociale:</p>
      <p>Bio des Haubner Stefan</p>
      <p>Lindenweg 14</p>
      <p>I-39099 Birkental</p>
      <p>IVA: IT04518230096</p>
      <p>CF.: HBNSTF88M12B952K</p>
      <p>Tel; +39 0471/228410 Handy/Cell; 3401187265</p>
      <p>https://www.natur-vemo.com/</p>
      <p>info@natur-vemo.com</p>
      <p class="imprint__lot">LottoNummer/CH nummer / Lotto n.: 123456</p>
      <p class="imprint__best">Mindestens haltbar bis / Da consumarsi entro:</p>
    </div>
    <div class="best-before-field"></div>

    <div class="product">
      <div class="product__art" role="img" aria-label="Illustration einer violetten Passionsblume auf grünem Grund"></div>
      <h1 class="product__name">Lavendel</h1>
      <p class="product__variant">fein · Lavanda fine</p>
      <p class="product__volume">10 ml</p>
    </div>

    <div class="usage">
      <div class="usage__block" lang="de">
        <p>100% natürliches etherisches Öl. Aroma-Kosmetikum zur Körperpflege.</p>
        <p><b>Anwendung:</b> Als Haut- u. Massageöl max 15 Tr. mit 50 ml z.B. Mandelöl mischen. Als Badezusatz 8-15 Tr. auf 4 EßI. Sahne oder Milch ins Badewasser geben.</p>
        <p>Nur in der angegeben Verdünnung anwenden! Nicht in die Augen oder auf die Schleimhäute bringen! Außer Reichweite von Kindern lagern. Abgefüllt in Italien</p>
      </div>
      <div class="usage__block" lang="it">
        <p>Olio essenziale 100% naturale. Cosmetico aromatico per la cura del corpo.</p>
        <p><b>Uso:</b> come olio per pelle e massaggi max 15 gocce in 50 ml p.es. di olio di mandorle. Nel bagno 8-15 gocce in 4 cucchiai di panna o latte.</p>
        <p>Usare solo nella diluizione indicata! Evitare il contatto con occhi e mucose! Tenere fuori dalla portata dei bambini. Imbottigliato in Italia</p>
      </div>
    </div>

    <div class="cut-frame"></div>
  </div>
</div>
</body>
</html>
```